Quill Physical Therapy Website

I would need a clean modern website built to showcase my Physical therapy brand and services. I would need a simple but descriptive website that can ultimately connect my patients to my electronic medical portal so they may book an appointment..

```html
<!DOCTYPE html>
<html lang="en">
<head>
<meta charset="utf-8">
<title>Quill Physical Therapy &amp; Wellness</title>
<link href="https://fonts.googleapis.com/css2?family=Montserrat:wght@400;500;600;700;800&family=Lato:wght@400;700&display=swap" rel="stylesheet">
<style>
:root{
  --teal:#13847a;
  --teal-dark:#0e6d65;
  --green:#8bc34a;
  --green-soft:#a6d36b;
  --navy:#2b3a42;
  --ink:#2e3338;
  --muted:#7d8589;
  --grey:#cfd2d3;
  --pale:#eef6f6;
  --white:#ffffff;
}
*{box-sizing:border-box;margin:0;padding:0}
html,body{width:1200px;height:4249px;overflow:hidden}
body{position:relative;background:var(--white);font-family:'Lato',sans-serif;color:var(--ink)}
.abs{position:absolute}
.h-font{font-family:'Montserrat',sans-serif}

/* header */
.topbar{left:0;top:0;width:1200px;height:110px;background:var(--white)}
.brand-badge{left:92px;top:0;width:200px;height:176px;background:var(--white);border-radius:0 0 100px 100px;display:flex;flex-direction:column;align-items:center;justify-content:flex-end;padding-bottom:26px;z-index:3}
.brand-dot{width:56px;height:56px;border-radius:50%;background:var(--teal);margin-bottom:12px}
.brand-name{font-family:'Montserrat',sans-serif;font-weight:800;font-size:36px;color:var(--teal);letter-spacing:1px;line-height:1}
.brand-sub{font-family:'Montserrat',sans-serif;font-weight:700;font-size:7.5px;color:var(--teal);margin-top:4px;letter-spacing:.3px}
.call{left:799px;top:0;width:285px;height:40px;background:var(--teal);color:var(--white);font-family:'Montserrat',sans-serif;font-weight:600;font-size:14px;display:flex;align-items:center;justify-content:center;gap:6px;border-radius:0 0 4px 4px}
.nav{left:364px;top:68px;display:flex;gap:0;font-family:'Montserrat',sans-serif;font-weight:600;font-size:12.5px;color:var(--ink)}
.nav a{color:inherit;text-decoration:none;position:relative;margin-right:45px}
.nav a:last-child{margin-right:0}
.nav a.active{color:var(--teal)}
.nav a.active::after{content:"";position:absolute;left:-2px;right:-2px;top:38px;height:4px;background:var(--green)}

/* hero */
.hero{left:0;top:110px;width:1200px;height:650px;background:linear-gradient(100deg,var(--teal) 0%,#2a9a78 28%,#7dbf60 45%,#d9c3b8 62%,#e8dcd6 100%)}
.hero-frame{left:99px;top:259px;width:141px;height:310px;border:4px solid var(--white);border-right:none}
.hero-frame::before,.hero-frame::after{content:"";position:absolute;right:0;width:4px;height:40px;background:var(--white)}
.hero-frame::before{top:0}.hero-frame::after{bottom:0}
.hero-welcome{left:115px;top:318px;font-family:'Montserrat',sans-serif;font-weight:400;font-size:25px;color:var(--white);letter-spacing:3px}
.hero-title{left:115px;top:348px;font-family:'Montserrat',sans-serif;font-weight:700;color:var(--white);line-height:1.1}
.hero-title .l1{font-size:50px;letter-spacing:1px;display:block}
.hero-title .l2{font-size:37px;letter-spacing:1.5px;display:block;margin-top:4px}
.btn{display:flex;align-items:center;justify-content:center;font-family:'Montserrat',sans-serif;font-weight:700;border-radius:30px}
.hero-btn{left:117px;top:467px;width:248px;height:50px;background:var(--green);color:var(--white);font-size:14px;letter-spacing:1px}
.arrow{top:395px;width:24px;height:40px}

/* about */
.about-photo{left:120px;top:770px;width:450px;height:600px;border-radius:40%;background:radial-gradient(ellipse at center,#c9d6da 0%,#e6eced 55%,rgba(255,255,255,0) 75%)}
.eyebrow{font-family:'Montserrat',sans-serif;font-weight:700;font-size:16px;letter-spacing:3.5px}
.about-eyebrow{left:597px;top:889px;color:var(--teal)}
.sec-title{font-family:'Montserrat',sans-serif;font-weight:700;color:var(--ink);letter-spacing:1.5px}
.about-title{left:596px;top:910px;font-size:36px}
.rule{height:4px;width:95px;background:var(--green)}
.about-rule{left:597px;top:960px}
.about-text{left:597px;top:990px;width:500px;font-family:'Montserrat',sans-serif;font-size:13.5px;line-height:29px;color:#555}
.about-btn{left:594px;top:1192px;width:168px;height:48px;border:2px solid var(--teal);color:var(--teal);font-size:13px;letter-spacing:1px;background:var(--white)}

/* services */
.services-bg{left:0;top:1320px;width:1200px;height:820px}
.serv-eyebrow{left:0;top:1458px;width:1200px;text-align:center;color:var(--white);font-size:15px;letter-spacing:4px}
.serv-title{left:0;top:1480px;width:1200px;text-align:center;color:var(--white);font-size:32px}
.serv-rule{left:546px;top:1527px}
.card-accent{width:120px;height:120px;background:var(--green)}
.card{top:1569px;width:316px;height:402px;color:var(--white);text-align:center}
.card-photo{width:100%;height:206px}
.card h3{font-family:'Montserrat',sans-serif;font-weight:600;font-size:19px;margin:26px 0 10px;letter-spacing:.5px}
.card p{font-family:'Montserrat',sans-serif;font-size:12.5px;line-height:19px;padding:0 44px}
.card .btn{width:130px;height:38px;border:2px solid var(--white);margin:22px auto 0;font-size:11px;letter-spacing:.8px}
.card.teal{background:var(--teal)}
.card.green{background:var(--green)}

/* why choose */
.why-title{left:0;top:2150px;width:1200px;text-align:center;font-size:28px}
.why-rule{left:545px;top:2193px;width:86px}
.why-ring{left:451px;top:2285px;width:296px;height:236px}
.why-core{left:483px;top:2263px;width:232px;height:232px;border-radius:50%;background:var(--white);box-shadow:0 8px 30px rgba(0,0,0,.08);display:flex;align-items:center;justify-content:center}
.why-core span{width:120px;height:120px;border-radius:50%;background:var(--teal)}
.feat-icon{width:72px;height:72px;border-radius:50%;background:linear-gradient(160deg,var(--green),var(--teal));display:flex;align-items:center;justify-content:center}
.feat{width:220px}
.feat h4{font-family:'Lato',sans-serif;font-weight:700;font-size:17px;color:var(--ink);margin-bottom:6px}
.feat p{font-size:13px;line-height:16.5px;color:var(--muted)}
.feat.left{text-align:right}

/* testimonials */
.testi-bg{left:0;top:2764px;width:1200px;height:520px;background:var(--pale)}
.testi-photo{left:0;top:2764px;width:470px;height:520px;background:linear-gradient(90deg,#8fb3c8 0%,#c8d8df 55%,rgba(238,246,246,0) 100%)}
.testi-title{left:340px;top:2822px;width:500px;text-align:center;font-size:29px}
.testi-rule{left:545px;top:2864px;width:92px}
.quote{top:2907px;width:302px;height:202px;background:var(--white);border:1px solid #d5e6e5;border-radius:6px;padding:36px 32px 0;font-family:'Montserrat',sans-serif;font-style:italic;font-size:12px;line-height:20px;color:#4f5a60}
.quote::after{content:"";position:absolute;left:56px;bottom:-11px;width:20px;height:20px;background:var(--white);border-right:1px solid #d5e6e5;border-bottom:1px solid #d5e6e5;transform:rotate(45deg)}
.reviewer{top:3130px;display:flex;align-items:center;gap:10px}
.avatar{width:46px;height:46px;border-radius:50%;background:#d9b39c}
.reviewer b{display:block;font-family:'Montserrat',sans-serif;font-size:12px;color:var(--teal);margin-bottom:2px}
.stars{color:#f5a623;font-size:20px;letter-spacing:1px;line-height:1}

/* booking */
.book-bg{left:0;top:3283px;width:1200px;height:584px;background:var(--teal)}
.book-photo{left:0;top:3283px;width:1200px;height:584px}
.book-eyebrow{left:110px;top:3364px;color:var(--white);font-size:16px;letter-spacing:3px}
.book-title{left:109px;top:3385px;color:var(--white);font-size:31px;letter-spacing:1.5px}
.field{left:105px;width:382px;height:45px;background:var(--white);border-radius:24px;padding:12px 0 0 25px;font-family:'Montserrat',sans-serif;font-weight:600;font-size:12px;color:#333}
.field.msg{height:98px;border-radius:18px}
.submit{left:110px;top:3713px;width:154px;height:40px;background:var(--green);color:var(--white);font-size:12.5px;letter-spacing:1px}

/* footer */
.foot-brand{left:128px;top:3928px;width:190px;display:flex;flex-direction:column;align-items:center}
.foot-brand .brand-dot{width:78px;height:78px}
.foot-brand .brand-name{font-size:54px}
.foot-brand .brand-sub{font-size:9.5px;color:var(--green)}
.foot-col h5{font-family:'Montserrat',sans-serif;font-weight:700;font-size:16px;color:var(--teal);margin-bottom:12px;letter-spacing:.3px}
.foot-col li{list-style:none;font-size:12.5px;color:#333;line-height:28px}
.contact li{display:flex;align-items:flex-start;gap:10px;line-height:23px}
.contact svg{flex:none;margin-top:4px}
.bottom{left:0;top:4196px;width:1200px;height:53px;background:var(--green);color:var(--white);font-size:10.5px;display:flex;align-items:center;justify-content:center}
.socials{right:152px;top:4210px;display:flex;gap:4px}
.socials span{width:26px;height:26px;border:1.5px solid var(--white);border-radius:50%}
</style>
</head>
<body>

<!-- header -->
<header class="abs topbar"></header>
<div class="abs brand-badge"><span class="brand-dot"></span><span class="brand-name">QUILL</span><span class="brand-sub">PHYSICAL THERAPY &amp; WELLNESS</span></div>
<div class="abs call">
  <svg width="16" height="16" viewBox="0 0 24 24"><path fill="#fff" d="M6.6 10.8a15 15 0 0 0 6.6 6.6l2.2-2.2c.3-.3.7-.4 1-.2 1.1.4 2.3.6 3.6.6.6 0 1 .4 1 1V20c0 .6-.4 1-1 1A17 17 0 0 1 3 4c0-.6.4-1 1-1h3.5c.6 0 1 .4 1 1 0 1.3.2 2.5.6 3.6.1.3 0 .7-.2 1z"/></svg>
  CALL US NOW +123 555 0190
</div>
<nav class="abs nav">
  <a class="active">HOME</a><a>ABOUT US</a><a>OUR SERVICES</a><a>WHY CHOOSE US</a><a>TESTIMONIALS</a><a>CONTACT US</a>
</nav>

<!-- hero -->
<section class="abs hero" role="img" aria-label="Photo of a seated patient holding a knee with a glowing skeletal overlay of the leg"></section>
<div class="abs hero-frame"></div>
<p class="abs hero-welcome">WELCOME TO</p>
<h1 class="abs hero-title"><span class="l1">QUILL PHYSICAL</span><span class="l2">THERAPY &amp; WELLNESS</span></h1>
<a class="abs btn hero-btn">BOOK APPOINTMENT</a>
<svg class="abs arrow" style="left:26px" viewBox="0 0 24 40"><path d="M20 4 6 20l14 16" fill="none" stroke="#fff" stroke-width="4"/></svg>
<svg class="abs arrow" style="left:1158px" viewBox="0 0 24 40"><path d="M4 4l14 16L4 36" fill="none" stroke="#fff" stroke-width="4"/></svg>

<!-- about -->
<div class="abs about-photo" role="img" aria-label="Therapist guiding a patient's arm stretch, softly faded into white"></div>
<p class="abs eyebrow about-eyebrow">WHO WE ARE</p>
<h2 class="abs sec-title about-title">ABOUT QUILL</h2>
<div class="abs rule about-rule"></div>
<p class="abs about-text">Lorem Ipsum is simply dummy text of the printing and typesetting industry. Lorem Ipsum has been the industry's standard dummy text ever since the 1500s, when an unknown printer took a galley of type and scrambled it to make a type specimen book. It has survived not only five centuries, but also the leap into electronic typesetting, remaining essentially unchanged. Lorem Ipsum is simply dummy.</p>
<a class="abs btn about-btn">LEARN MORE</a>

<!-- services -->
<svg class="abs services-bg" viewBox="0 0 1200 820" preserveAspectRatio="none">
  <polygon points="0,105 1200,6 1200,712 0,804" fill="#2b3a42"/>
  <polygon points="0,25 460,65 0,107" fill="#8bc34a"/>
  <polygon points="660,760 1200,715 1200,790" fill="#cfd2d3"/>
</svg>
<p class="abs eyebrow serv-eyebrow">WHAT WE DO</p>
<h2 class="abs sec-title serv-title">SERVICES PROVIDE</h2>
<div class="abs rule serv-rule"></div>

<div class="abs card-accent" style="left:94px;top:1558px"></div>
<div class="abs card-accent" style="left:982px;top:1860px"></div>

<article class="abs card teal" style="left:105px">
  <div class="card-photo" role="img" aria-label="Therapist massaging the back of a patient lying on a table" style="background:linear-gradient(135deg,#bfc3c5,#8d9396)"></div>
  <h3>PHYSICAL THERAPY</h3>
  <p>Lorem ipsum dolor sit amet, consectetur adipiscing elit sed do.Lorem ipsum dolor sit amet</p>
  <a class="btn">LEARN MORE</a>
</article>
<article class="abs card green" style="left:439px">
  <div class="card-photo" role="img" aria-label="Patient's back with a highlighted glowing spine under a therapist's hands" style="background:linear-gradient(135deg,#e6e6e6,#c9a99a)"></div>
  <h3>INJURY PAIN</h3>
  <p>Lorem ipsum dolor sit amet, consectetur adipiscing elit sed do.Lorem ipsum dolor sit amet</p>
  <a class="btn">LEARN MORE</a>
</article>
<article class="abs card teal" style="left:776px">
  <div class="card-photo" role="img" aria-label="Close view of hands massaging a leg" style="background:linear-gradient(135deg,#e9c1a8,#b97e62)"></div>
  <h3>WELLNESS THERAPY</h3>
  <p>Lorem ipsum dolor sit amet, consectetur adipiscing elit sed do.Lorem ipsum dolor sit amet</p>
  <a class="btn">LEARN MORE</a>
</article>

<!-- why choose -->
<h2 class="abs sec-title why-title">WHY CHOOSE QUILL</h2>
<div class="abs rule why-rule"></div>
<svg class="abs why-ring" viewBox="0 0 296 236">
  <path d="M30 12 A150 150 0 0 0 266 12" fill="none" stroke="#8bc34a" stroke-width="3"/>
  <path d="M30 12 A150 150 0 0 0 148 226" fill="none" stroke="#8bc34a" stroke-width="3"/>
  <g fill="#fff" stroke="#13847a" stroke-width="2">
    <circle cx="30" cy="12" r="6"/><circle cx="263" cy="12" r="6"/>
    <circle cx="12" cy="150" r="6"/><circle cx="282" cy="150" r="6"/>
    <circle cx="148" cy="226" r="6"/>
  </g>
</svg>
<div class="abs why-core"><span></span></div>

<div class="abs feat left" style="left:136px;top:2257px"><h4>Injury Pain Relief</h4><p>Donec convallis pede venenatis nibh Duis quam Nam eget lacus Aliquam erat volutpat Quisque dignissi</p></div>
<div class="abs feat-icon" style="left:379px;top:2262px"><svg width="34" height="34" viewBox="0 0 24 24" fill="none" stroke="#fff" stroke-width="1.5"><rect x="3" y="14" width="18" height="5" rx="1"/><circle cx="12" cy="7" r="3"/></svg></div>

<div class="abs feat left" style="left:133px;top:2425px"><h4>Therapy Specialist</h4><p>Donec convallis pede venenatis nibh Duis quam Nam eget lacus Aliquam erat volutpat Quisque dignissi</p></div>
<div class="abs feat-icon" style="left:370px;top:2420px"><svg width="34" height="34" viewBox="0 0 24 24" fill="none" stroke="#fff" stroke-width="1.5"><circle cx="12" cy="12" r="7"/><circle cx="12" cy="12" r="2.5"/></svg></div>

<div class="abs feat-icon" style="left:749px;top:2262px"><svg width="34" height="34" viewBox="0 0 24 24" fill="none" stroke="#fff" stroke-width="1.5"><circle cx="6" cy="16" r="3"/><circle cx="18" cy="16" r="3"/><path d="M6 16l6-8 6 8"/></svg></div>
<div class="abs feat" style="left:834px;top:2257px"><h4>Total body composition</h4><p>Donec convallis pede venenatis nibh Duis quam Nam eget lacus Aliquam erat volutpat Quisque dignissi</p></div>

<div class="abs feat-icon" style="left:757px;top:2420px"><svg width="34" height="34" viewBox="0 0 24 24" fill="none" stroke="#fff" stroke-width="1.5"><path d="M12 20s-8-5-8-11a4 4 0 0 1 8-1 4 4 0 0 1 8 1c0 6-8 11-8 11z"/></svg></div>
<div class="abs feat" style="left:841px;top:2425px"><h4>Wellness Therapy</h4><p>Donec convallis pede venenatis nibh Duis quam Nam eget lacus Aliquam erat volutpat Quisque dignissi</p></div>

<div class="abs feat-icon" style="left:564px;top:2543px"><svg width="34" height="34" viewBox="0 0 24 24" fill="none" stroke="#fff" stroke-width="1.5"><circle cx="12" cy="12" r="8"/><path d="M5 9c5 0 9 3 11 10M9 4c3 3 5 8 5 14"/></svg></div>
<div class="abs feat" style="left:470px;top:2626px;width:260px;text-align:center"><h4>Sports Therapy</h4><p>Donec convallis pede venenatis nibh Duis quam Nam eget lacus Aliquam erat</p></div>

<!-- testimonials -->
<section class="abs testi-bg"></section>
<div class="abs testi-photo" role="img" aria-label="Therapist in blue scrubs helping a senior man stretch his arm"></div>
<h2 class="abs sec-title testi-title">WHAT PEOPLE SAYS</h2>
<div class="abs rule testi-rule"></div>
<blockquote class="abs quote" style="left:439px">Lorem ipsum dolor sit amet, consectetur adipiscing elit, sed do eiusmod tempor incididunt ut labore et dolore magna aliqua. Ut enim ad minim veniam, quis nostrud exercitation ullamco laboris nisi ut aliquip ex ea commodo conseq</blockquote>
<blockquote class="abs quote" style="left:756px">Lorem ipsum dolor sit amet, consectetur adipiscing elit, sed do eiusmod tempor incididunt ut labore et dolore magna aliqua. Ut enim ad minim veniam, quis nostrud exercitation ullamco laboris nisi ut aliquip ex ea commodo conseq</blockquote>
<div class="abs reviewer" style="left:475px"><span class="avatar" role="img" aria-label="Reviewer portrait"></span><div><b>Dana Merrow</b><span class="stars">★★★★★</span></div></div>
<div class="abs reviewer" style="left:792px"><span class="avatar" role="img" aria-label="Reviewer portrait" style="background:#d7a088"></span><div><b>Dana Merrow</b><span class="stars">★★★★★</span></div></div>

<!-- booking -->
<section class="abs book-bg"></section>
<svg class="abs book-photo" viewBox="0 0 1200 584" role="img" aria-label="Therapist's hands pressing a patient's shoulder with a glowing highlighted spine">
  <defs><linearGradient id="skin" x1="0" y1="0" x2="1" y2="1"><stop offset="0" stop-color="#c98a6c"/><stop offset=".5" stop-color="#e98c6a"/><stop offset="1" stop-color="#9c5d45"/></linearGradient></defs>
  <path d="M700 0 C560 160 560 420 620 584 L1200 584 L1200 0 Z" fill="#8bc34a"/>
  <path d="M718 0 C585 170 585 420 644 584 L1200 584 L1200 0 Z" fill="url(#skin)"/>
</svg>
<p class="abs eyebrow book-eyebrow">GET IN TOUCH</p>
<h2 class="abs sec-title book-title">BOOK APPOINTMENT</h2>
<div class="abs field" style="top:3448px">Name*</div>
<div class="abs field" style="top:3498px">Email address*</div>
<div class="abs field" style="top:3548px">Phone*</div>
<div class="abs field msg" style="top:3600px">Message</div>
<a class="abs btn submit">SUBMIT NOW</a>

<!-- footer -->
<div class="abs foot-brand"><span class="brand-dot" style="margin-bottom:18px"></span><span class="brand-name">QUILL</span><span class="brand-sub">PHYSICAL THERAPY &amp; WELLNESS</span></div>
<div class="abs foot-col" style="left:422px;top:3940px"><h5>NAVIGATE</h5><ul><li>Home</li><li>About Us</li><li>Our Services</li><li>New Products</li><li>Contact Us</li></ul></div>
<div class="abs foot-col" style="left:619px;top:3940px"><h5>RESOURCES</h5><ul><li>News</li><li>Testimonials</li><li>Privacy Policy</li><li>Terms &amp; Condition</li></ul></div>
<div class="abs foot-col contact" style="left:837px;top:3940px"><h5>CONTACT US</h5><ul>
  <li><svg width="12" height="16" viewBox="0 0 12 16"><path d="M6 0a6 6 0 0 0-6 6c0 4.5 6 10 6 10s6-5.5 6-10a6 6 0 0 0-6-6zm0 8.5A2.5 2.5 0 1 1 6 3.5a2.5 2.5 0 0 1 0 5z" fill="#13847a"/></svg><span>Office North | 14 Harbor Lane<br>Office South | 82 Mill Road</span></li>
  <li><svg width="13" height="13" viewBox="0 0 24 24"><path fill="#13847a" d="M6.6 10.8a15 15 0 0 0 6.6 6.6l2.2-2.2c.3-.3.7-.4 1-.2 1.1.4 2.3.6 3.6.6.6 0 1 .4 1 1V20c0 .6-.4 1-1 1A17 17 0 0 1 3 4c0-.6.4-1 1-1h3.5c.6 0 1 .4 1 1 0 1.3.2 2.5.6 3.6.1.3 0 .7-.2 1z"/></svg><span>Tel: (1300) 555 0147</span></li>
  <li><svg width="14" height="11" viewBox="0 0 14 11"><rect width="14" height="11" rx="1" fill="#13847a"/><path d="M1 1l6 5 6-5" fill="none" stroke="#fff"/></svg><span>Email: hello@quillphysio.com</span></li>
</ul></div>
<footer class="abs bottom">© 2021 Quill Studio | All Rights Reserved &nbsp;|&nbsp; Terms &amp; Condition</footer>
<div class="abs socials"><span></span><span></span><span></span></div>

</body>
</html>
```